Maplecrest Disability - Social Security Disability Attorneys

Our company is expanding to attract clients nationwide for our social security disability practice. We have a logo, but I am looking for a creative and elegant letterhead that projects an image of being technologically advanced but still professional enough for the legal field. I am looking for the "wow factor" combined with this is still professional enough for a law practice.

Requesting letterhead and business card design
Updates

Had to update and change the logo. The previous logo had a typo. Please send updates with the new logo for consideration. The letterhead and business cards should be professional enough to be used for a law firm. Thanks.

Industry/Entity Type

Law Practice, Law Firm, Healthcare Industry, Government

Colors

Designer to choose colors to be used in the design.

Requirements
Nice to have
• **Please create a vertical design for the business card**

```html
<!DOCTYPE html>
<html lang="en">
<head>
<meta charset="utf-8">
<title>Maplecrest Disability – Business Card</title>
<link rel="stylesheet" href="https://fonts.googleapis.com/css2?family=Cinzel:wght@600&family=Mulish:wght@400&display=swap">
<style>
  :root {
    --page-bg: #d9d4cc;
    --blue-light: #2b3fcf;
    --blue-deep: #0a1785;
    --red: #c3260f;
    --frost-light: #eeeae6;
    --frost-mid: #d6d0ca;
    --ink-light: #e9ecf7;
    --ink-navy: #16207a;
  }
  html, body {
    margin: 0;
    padding: 0;
    width: 1200px;
    height: 969px;
    overflow: hidden;
    background: var(--page-bg);
  }
  .canvas {
    position: relative;
    width: 1200px;
    height: 969px;
  }
  .card {
    position: absolute;
    left: 100px;
    top: 200px;
    width: 1000px;
    height: 570px;
    border-radius: 26px;
    overflow: hidden;
    box-shadow: 0 18px 40px rgba(0,0,0,0.18);
  }
  .card-art {
    position: absolute;
    inset: 0;
    width: 1000px;
    height: 570px;
  }
  .holder {
    position: absolute;
    left: 65px;
    top: 156px;
    color: var(--ink-light);
  }
  .holder-name {
    font-family: "Cinzel", serif;
    font-weight: 600;
    font-size: 30px;
    letter-spacing: 0.5px;
    margin: 0;
    line-height: 1;
  }
  .holder-title {
    font-family: "Mulish", sans-serif;
    font-size: 19px;
    margin: 6px 0 0;
  }
  .address {
    font-family: "Mulish", sans-serif;
    font-size: 19px;
    line-height: 28px;
    margin: 24px 0 0;
  }
  .contacts {
    list-style: none;
    padding: 0;
    margin: 14px 0 0;
    font-family: "Mulish", sans-serif;
    font-size: 19px;
  }
  .contacts li {
    display: flex;
    align-items: center;
    height: 28px;
  }
  .contacts svg {
    width: 18px;
    height: 18px;
    margin-right: 19px;
    fill: var(--ink-light);
    flex: none;
  }
  .brand {
    position: absolute;
    left: 526px;
    width: 400px;
    top: 282px;
    text-align: center;
    color: var(--ink-navy);
    font-family: "Mulish", sans-serif;
    font-weight: 400;
  }
  .brand-name {
    font-size: 32px;
    margin: 0;
    line-height: 1.1;
    white-space: nowrap;
  }
  .brand-tagline {
    font-size: 13px;
    letter-spacing: 1px;
    margin: 8px 0 0;
    white-space: nowrap;
  }
</style>
</head>
<body>
<div class="canvas">
  <div class="card">
    <svg class="card-art" viewBox="0 0 1000 570" aria-hidden="true">
      <defs>
        <linearGradient id="frost" x1="0" y1="0" x2="1" y2="1">
          <stop offset="0" stop-color="var(--frost-light)"/>
          <stop offset="1" stop-color="var(--frost-mid)"/>
        </linearGradient>
        <radialGradient id="blueGlow" cx="0.35" cy="0.35" r="0.8">
          <stop offset="0" stop-color="var(--blue-light)"/>
          <stop offset="1" stop-color="var(--blue-deep)"/>
        </radialGradient>
      </defs>
      <rect class="frost-panel" width="1000" height="570" fill="url(#frost)"/>
      <path class="red-sweep" d="M0,0 H512 C440,95 416,225 455,338 C502,458 622,532 762,570 H0 Z" fill="var(--red)"/>
      <path class="blue-panel" d="M0,0 H505 C440,90 410,220 445,330 C480,440 560,520 650,570 H0 Z" fill="url(#blueGlow)"/>
    </svg>

    <div class="holder">
      <h1 class="holder-name">DANIEL WHITMORE</h1>
      <p class="holder-title">Founder &amp; CEO</p>
      <p class="address">2215 Cedar Hollow Road<br>Anchorage, Alaska 99508</p>
      <ul class="contacts">
        <li><svg viewBox="0 0 24 24"><path d="M6.6 10.8a15.1 15.1 0 0 0 6.6 6.6l2.2-2.2c.3-.3.7-.4 1-.2 1.1.4 2.3.6 3.6.6.6 0 1 .4 1 1V20c0 .6-.4 1-1 1A17 17 0 0 1 3 4c0-.6.4-1 1-1h3.5c.6 0 1 .4 1 1 0 1.3.2 2.5.6 3.6.1.3 0 .7-.2 1z"/></svg>555-214-8830</li>
        <li><svg viewBox="0 0 24 24"><path d="M7 1h10a2 2 0 0 1 2 2v18a2 2 0 0 1-2 2H7a2 2 0 0 1-2-2V3a2 2 0 0 1 2-2zm0 3v14h10V4zm5 15.5a1 1 0 1 0 0 2 1 1 0 0 0 0-2z"/></svg>555-731-2096</li>
        <li><svg viewBox="0 0 24 24"><path d="M2 5h20v14H2zm2 2v.5l8 5 8-5V7zm0 2.8V17h16V9.8l-8 5z"/></svg>info@maplecrestdisability.com</li>
        <li><svg viewBox="0 0 24 24"><path d="M12 2a10 10 0 1 0 0 20 10 10 0 0 0 0-20zm-1 17.9A8 8 0 0 1 4.2 10.6L9 15v1a2 2 0 0 0 2 2zm6.9-2.5A2 2 0 0 0 16 16h-1v-3a1 1 0 0 0-1-1H8v-2h2a1 1 0 0 0 1-1V7h2a2 2 0 0 0 2-2v-.4a8 8 0 0 1 2.9 12.8z"/></svg>www.maplecrestdisability.com</li>
      </ul>
    </div>

    <div class="brand">
      <p class="brand-name">Maplecrest Disability</p>
      <p class="brand-tagline">Social Security Disability Attorneys</p>
    </div>
  </div>
</div>
</body>
</html>
```